Association qui souhaite améliorer l'accès aux personnes en situation de handicap

Nous sommes une association qui a pour objectif d'améliorer l'accessibilité, augmenter l'offre des activités réalisables dans notre région touristique.
Nous souhaitons réaliser un site internet afin de pouvoir communiquer sur notre association. Nous avons déjà conçu notre flyer sur Plumotrix. Nous souhaiterions une base graphique se rapportant à celui-ci. C'est possible de tout retravailler mais nous souhaitons tout de même retrouver la charte graphique ou code couleur du flyer.
Il nous faudrait quelques pages:
- 1 page : Acceuil / Présentation (Home), Il y aurait le descriptif de l'association, avec ses objectifs à +/- moyen terme
- 1 page : Nos réalisations, celle-ci présenterait les éléments que nous avons réalisés avec des zones de textes et des images classées chronologiquement au fur et à mesure des nouveautés
- 1 page : Media, comme la précédente, mais ou on pourrait voir ou lire sur les divers médias qui parlent de nous
- 1 page : Evenements : c'est une page pour présenter divers activités que nous allons organiser
- 1 page : Contact qui indique comment nous contacter et avec la présentation des 5 ou 6 membres du comité
- 1 link donate : qui arrive sur un formulaire de donnée que l'on pourra faire évoluer sur un système de payement par la suite. Cette bannière doit se retrouver sur toutes les pages
Il est nécessaire que se design puisse être transféré sur une lecture sur téléphone mobile
Personnes en situation de handicap
Associatif

```html
<!DOCTYPE html>
<html lang="en">
<head>
<meta charset="utf-8">
<title>OpenWay Association</title>
<link href="https://fonts.googleapis.com/css2?family=Oswald:wght@500;600&family=Lexend:wght@300;400;500&display=swap" rel="stylesheet">
<style>
:root{
  --red:#c4161c;
  --red-dark:#a51117;
  --ink:#2a2a2a;
  --dark:#2c3034;
  --dark-2:#24282b;
  --muted:#4a4a4a;
  --light:#f2f2f4;
  --white:#ffffff;
  --line:#e2e2e6;
}
*{margin:0;padding:0;box-sizing:border-box}
html,body{width:1200px;height:4839px;overflow:hidden}
body{position:relative;background:var(--white);font-family:"Lexend",sans-serif;color:var(--ink);font-weight:300}
.abs{position:absolute}
.head{font-family:"Oswald",sans-serif;font-weight:600;text-transform:uppercase;letter-spacing:.5px}
.red{color:var(--red)}
.arrow{display:inline-block;width:16px;height:12px;vertical-align:middle;margin-left:12px}

/* header */
.topbar{top:0;left:0;width:1200px;height:4px;background:var(--red)}
.topbar-info{top:0;left:640px;width:560px;height:44px;background:var(--red);clip-path:polygon(22px 0,100% 0,100% 100%,0 100%);color:var(--white);font-size:14px;display:flex;align-items:center;padding-left:24px;gap:10px}
.topbar-info b{font-weight:500}
.topbar-info .sep{opacity:.6}
.social-dot{width:12px;height:12px;border-radius:50%;background:var(--white);display:inline-block}
.brand{top:30px;left:92px;display:flex;align-items:center;gap:10px}
.brand-square{width:14px;height:14px;background:var(--red)}
.brand-name{font-family:"Oswald",sans-serif;font-weight:600;font-size:24px;color:var(--ink);line-height:1}
.nav{top:76px;left:583px;display:flex;gap:30px;font-size:14px;font-weight:500;text-transform:uppercase;color:var(--ink)}
.nav .active{position:relative}
.nav .active::before{content:"";position:absolute;left:50%;top:-20px;width:10px;height:10px;background:var(--red);transform:translateX(-50%)}

/* hero */
.hero-photo{top:126px;left:0;width:1200px;height:561px;background:linear-gradient(90deg,#3a3028 0%,#5a4a3c 35%,#9a8168 60%,#c9b7a1 100%)}
.hero-shade{top:126px;left:0;width:640px;height:561px;background:linear-gradient(90deg,rgba(20,20,20,.55),rgba(20,20,20,0))}
.hero-kicker{top:256px;left:92px;font-size:30px;color:var(--white);font-weight:500}
.hero-title{top:284px;left:92px;font-size:70px;line-height:1.1;color:var(--white)}
.hero-text{top:376px;left:92px;width:440px;font-size:17px;line-height:31px;color:var(--white)}
.btn-red{background:var(--red);color:var(--white);font-family:"Oswald",sans-serif;font-weight:500;text-transform:uppercase;display:flex;align-items:center;justify-content:center;font-size:16px}
.hero-btn{top:500px;left:92px;width:229px;height:54px}
.slide-arrow{width:38px;height:90px;background:#1c1c1c;display:flex;align-items:center;justify-content:center}
.hero-decor{top:394px;left:760px}

/* welcome */
.cross-icon{top:939px;left:92px;width:42px;height:42px;background:var(--red)}
.cross-icon::before,.cross-icon::after{content:"";position:absolute;background:var(--white)}
.cross-icon::before{left:17px;top:9px;width:8px;height:24px}
.cross-icon::after{left:9px;top:17px;width:24px;height:8px}
.section-title{font-size:46px;line-height:52px;color:var(--ink)}
.welcome-title{top:990px;left:92px}
.welcome-text{top:1114px;left:92px;width:510px;font-size:17px;line-height:30px;color:var(--muted)}
.welcome-photo{top:858px;left:680px;width:426px;height:513px;background:linear-gradient(160deg,#c8c0b5,#8c9aa8 50%,#4a5a6e);clip-path:polygon(0 0,100% 0,100% 78%,0 100%)}

/* achievements */
.ach-bg{top:1459px;left:0;width:1200px;height:866px;background:linear-gradient(180deg,#34383c,var(--dark))}
.mark-square{width:30px;height:30px;border:4px solid var(--red)}
.center-title{width:1200px;text-align:center;font-size:46px;color:var(--white)}
.center-sub{width:1200px;text-align:center;font-size:17px;line-height:31px;color:var(--white)}
.ach-card{top:1784px;width:322px;height:338px}
.ach-photo{position:absolute;inset:0;height:338px}
.ach-label{position:absolute;left:22px;right:0;bottom:0;height:66px;background:var(--white);clip-path:polygon(22px 0,100% 0,100% 100%,0 100%);font-family:"Oswald",sans-serif;font-weight:500;font-size:19px;text-transform:uppercase;display:flex;align-items:center;justify-content:center;color:var(--ink)}
.ach-card.featured .ach-label{background:var(--red);color:var(--white)}
.ach-go{position:absolute;right:0;bottom:58px;width:45px;height:42px;background:var(--red);display:flex;align-items:center;justify-content:center}
.ach-card.featured .ach-go{background:var(--white)}
.btn-outline-light{top:2182px;left:458px;width:284px;height:54px;border:2px solid var(--white);color:var(--white);font-family:"Oswald",sans-serif;font-weight:500;font-size:17px;text-transform:uppercase;display:flex;align-items:center;justify-content:center}
.side-arrow{width:50px;height:20px}

/* media */
.media-title{top:2462px;left:92px}
.media-text{top:2534px;left:92px;width:560px;font-size:17px;line-height:31px;color:var(--muted)}
.media-btn{top:2470px;left:926px;width:180px;height:54px}
.media-card{width:498px;height:257px;border:1px solid var(--line);border-radius:6px;background:var(--white);box-shadow:0 4px 14px rgba(0,0,0,.05)}
.media-photo{position:absolute;left:12px;top:12px;width:165px;height:232px}
.media-body{position:absolute;left:198px;top:28px;width:290px}
.media-body h3{font-family:"Oswald",sans-serif;font-weight:500;font-size:19px;line-height:28px;text-transform:uppercase;color:var(--ink);white-space:nowrap}
.media-body p{margin-top:12px;font-size:16px;line-height:30px;color:var(--muted);white-space:nowrap}
.btn-outline-red{margin-top:14px;width:172px;height:44px;border:2px solid var(--red);color:var(--red);font-family:"Oswald",sans-serif;font-weight:500;font-size:16px;text-transform:uppercase;display:flex;align-items:center;justify-content:center}

/* events */
.events-shape{top:3260px;left:0}
.event-card{top:3747px;width:322px;height:475px;background:var(--white)}
.event-photo{position:absolute;left:0;top:0;width:322px;height:225px}
.event-date{position:absolute;right:18px;top:18px;width:54px;height:70px;background:var(--red);color:var(--white);text-align:center}
.event-date .day{font-family:"Oswald",sans-serif;font-weight:500;font-size:26px;line-height:40px;display:block}
.event-date .mon{display:block;margin:0 6px;background:var(--white);color:var(--ink);font-size:12px;font-weight:500;line-height:20px;text-transform:uppercase}
.event-body{position:absolute;left:25px;top:250px;width:290px}
.event-by{font-size:13px;color:var(--muted)}
.event-body h3{margin-top:10px;font-family:"Oswald",sans-serif;font-weight:500;font-size:19px;line-height:28px;text-transform:uppercase;color:var(--ink);white-space:nowrap}
.event-body p{margin-top:12px;font-size:16px;line-height:30px;color:var(--muted);white-space:nowrap}
.event-more{margin-top:22px;font-family:"Oswald",sans-serif;font-weight:500;font-size:16px;color:var(--red);text-transform:uppercase;display:flex;align-items:center}

/* donate */
.footer-bg{top:4375px;left:0;width:1200px;height:464px;background:var(--light)}
.donate-band{top:4316px;left:94px;width:1012px;height:131px;background:linear-gradient(90deg,var(--red-dark),var(--red));clip-path:polygon(22px 0,96% 0,100% 100%,0 100%);box-shadow:0 10px 20px rgba(0,0,0,.2)}
.donate-line{top:4316px;left:94px;width:264px;height:2px;background:rgba(255,255,255,.3)}
.donate-text{top:4346px;left:184px;color:var(--white)}
.donate-text .s1{font-size:27px;line-height:34px;display:block}
.donate-text .s2{font-size:34px;line-height:42px;display:block}
.donate-divider{top:4346px;left:665px;width:2px;height:80px;background:rgba(255,255,255,.7)}
.donate-btn{top:4359px;left:798px;width:216px;height:53px;background:var(--dark-2);color:var(--white);font-family:"Oswald",sans-serif;font-weight:500;font-size:16px;text-transform:uppercase;display:flex;align-items:center;justify-content:center}

/* footer */
.footer-brand{top:4553px;left:92px}
.footer-social{top:4644px;left:92px;display:flex;gap:14px}
.footer-social span{width:44px;height:44px;border:2px solid var(--ink);border-radius:6px;display:flex;align-items:center;justify-content:center}
.footer-social span::after{content:"";width:10px;height:10px;background:var(--ink);border-radius:50%}
.footer-col h4{font-family:"Oswald",sans-serif;font-weight:500;font-size:22px;text-transform:uppercase;color:var(--ink)}
.footer-col ul{list-style:none;margin-top:18px}
.footer-col li{font-size:15px;line-height:33px;color:var(--ink)}
.contact-row{display:flex;gap:18px;margin-top:18px;font-size:15px;line-height:27px}
.contact-ico{width:42px;height:42px;border-radius:50%;background:var(--red);flex:none;display:flex;align-items:center;justify-content:center}
.footer-rule{top:4780px;left:92px;width:1014px;height:1px;background:#d6d6da}
.copyright{top:4800px;left:0;width:1200px;text-align:center;font-size:13px;color:var(--muted)}
</style>
</head>
<body>

<!-- header -->
<div class="abs topbar"></div>
<div class="abs topbar-info">
  <svg width="16" height="16" viewBox="0 0 24 24" fill="none" stroke="#fff" stroke-width="2"><path d="M22 16.9v3a2 2 0 0 1-2.2 2 19.8 19.8 0 0 1-8.6-3.1 19.5 19.5 0 0 1-6-6A19.8 19.8 0 0 1 2.1 4.2 2 2 0 0 1 4.1 2h3a2 2 0 0 1 2 1.7c.1.9.4 1.8.7 2.7a2 2 0 0 1-.5 2.1L8 9.8a16 16 0 0 0 6 6l1.3-1.3a2 2 0 0 1 2.1-.5c.9.3 1.8.6 2.7.7a2 2 0 0 1 1.7 2z"/></svg>
  <span class="sep">|</span>
  <span>Call Us: <b>024-718-3356</b></span>
  <span style="margin-left:44px">Stay with us:</span>
  <span class="social-dot"></span><span class="social-dot"></span><span class="social-dot"></span>
</div>
<div class="abs brand">
  <span class="brand-square"></span>
  <span class="brand-name">OPENWAY ASSOCIATION</span>
</div>
<nav class="abs nav">
  <span class="active">Home</span>
  <span>Our Achievements</span>
  <span>Media</span>
  <span>Events</span>
  <span>Contact</span>
</nav>

<!-- hero -->
<div class="abs hero-photo" role="img" aria-label="Photo of smiling friends hugging a woman in a wheelchair outdoors"></div>
<div class="abs hero-shade"></div>
<div class="abs hero-kicker head">Rejoin the</div>
<div class="abs hero-title head">Association</div>
<p class="abs hero-text">Friends living in the region who are committed to making the Haut-Vallon region as accessible as possible to people with disabilities.</p>
<div class="abs hero-btn btn-red">Contact us now
  <svg class="arrow" viewBox="0 0 16 12" fill="none" stroke="#fff" stroke-width="2"><path d="M0 6h14M9 1l5 5-5 5"/></svg>
</div>
<div class="abs slide-arrow" style="top:278px;left:0">
  <svg width="12" height="20" viewBox="0 0 12 20" fill="none" stroke="#fff" stroke-width="3"><path d="M10 2 2 10l8 8"/></svg>
</div>
<div class="abs slide-arrow" style="top:278px;left:1162px">
  <svg width="12" height="20" viewBox="0 0 12 20" fill="none" stroke="#fff" stroke-width="3"><path d="m2 2 8 8-8 8"/></svg>
</div>
<svg class="abs hero-decor" width="440" height="386" viewBox="0 0 440 386"><polygon points="440,0 440,386 40,293" fill="var(--red)"/></svg>

<!-- welcome -->
<div class="abs cross-icon"></div>
<h2 class="abs welcome-title section-title head">Welcome to<br>OpenWay All <span class="red">Association</span></h2>
<p class="abs welcome-text">Lorem ipsum dolor sit ameti consectetur adipisicing elit<br>sed do eiusmod tempor incididunt ut labore et doloreu<br>magna aliqua. Ut enim ad minim veniam, quis nostrud<br>exercitation ullamco laboris nisi ut aliquip ex ea comon<br>consequat. Duis aute irure dolor in reprehenderit. Ut ito<br>enim ad minim veniam, quis nostrud exercitation.</p>
<div class="abs welcome-photo" role="img" aria-label="Photo of a carer helping a woman with crutches stand up"></div>

<!-- achievements -->
<section class="abs ach-bg" aria-label="Our achievements"></section>
<div class="abs mark-square" style="top:1545px;left:585px"></div>
<h2 class="abs center-title head" style="top:1610px;left:0">Our Achievements</h2>
<p class="abs center-sub" style="top:1675px;left:0">Lorem ipsum dolor sit ameti consectetur adipisicing elit<br>sed do eiusmod tempor incididunt ut labore et</p>
<svg class="abs side-arrow" style="top:1943px;left:22px" viewBox="0 0 50 20" fill="none" stroke="#fff" stroke-width="2"><path d="M48 10H2M10 2 2 10l8 8"/></svg>
<svg class="abs side-arrow" style="top:1943px;left:1128px" viewBox="0 0 50 20" fill="none" stroke="#fff" stroke-width="2"><path d="M2 10h46M40 2l8 8-8 8"/></svg>

<div class="abs ach-card" style="left:92px">
  <div class="ach-photo" role="img" aria-label="Photo of a smiling older man in a cap and sunglasses" style="background:linear-gradient(180deg,#5f7d3a,#c9895f 60%,#e07a4f)"></div>
  <div class="ach-go"><svg width="16" height="12" viewBox="0 0 16 12" fill="none" stroke="#fff" stroke-width="2"><path d="M0 6h14M9 1l5 5-5 5"/></svg></div>
  <div class="ach-label">Lorem ipsum dolar sit</div>
</div>
<div class="abs ach-card featured" style="left:439px">
  <div class="ach-photo" role="img" aria-label="Photo of a laughing boy in a classroom" style="background:linear-gradient(180deg,#b49a6c,#8aa0b8 60%,#6c88a8)"></div>
  <div class="ach-go"><svg width="16" height="12" viewBox="0 0 16 12" fill="none" stroke="#c4161c" stroke-width="2"><path d="M0 6h14M9 1l5 5-5 5"/></svg></div>
  <div class="ach-label">Lorem ipsum dolar sit</div>
</div>
<div class="abs ach-card" style="left:785px">
  <div class="ach-photo" role="img" aria-label="Photo of a smiling older woman in a wheelchair" style="background:linear-gradient(180deg,#d8d8d6,#a9b6c4 60%,#8ea4bc)"></div>
  <div class="ach-go"><svg width="16" height="12" viewBox="0 0 16 12" fill="none" stroke="#fff" stroke-width="2"><path d="M0 6h14M9 1l5 5-5 5"/></svg></div>
  <div class="ach-label">Lorem ipsum dolar sit</div>
</div>
<div class="abs btn-outline-light">View all achievements
  <svg class="arrow" viewBox="0 0 16 12" fill="none" stroke="#fff" stroke-width="2"><path d="M0 6h14M9 1l5 5-5 5"/></svg>
</div>

<!-- media -->
<div class="abs mark-square" style="top:2420px;left:92px"></div>
<h2 class="abs media-title section-title head">Our <span class="red">Media</span></h2>
<p class="abs media-text">Lorem ipsum dolor sit ameti consectetur adipisicing elit<br>sed do eiusmod tempor incididunt ut labore et</p>
<div class="abs media-btn btn-red">View more
  <svg class="arrow" viewBox="0 0 16 12" fill="none" stroke="#fff" stroke-width="2"><path d="M0 6h14M9 1l5 5-5 5"/></svg>
</div>

<article class="abs media-card" style="top:2644px;left:92px">
  <div class="media-photo" role="img" aria-label="Photo of a woman with a white cane in a park" style="background:linear-gradient(160deg,#6f7f4f,#b07a3e 60%,#3e4a36)"></div>
  <div class="media-body">
    <h3>Sed ut perspiciatis under a<br>omnis iste natus error to</h3>
    <p>Lorem ipsum dolor sit ameti top<br>sed consectetur adipisicing elit</p>
    <div class="btn-outline-red">View more
      <svg class="arrow" viewBox="0 0 16 12" fill="none" stroke="#c4161c" stroke-width="2"><path d="M0 6h14M9 1l5 5-5 5"/></svg></div>
  </div>
</article>
<article class="abs media-card" style="top:2644px;left:608px">
  <div class="media-photo" role="img" aria-label="Photo of a smiling young girl" style="background:linear-gradient(160deg,#d9d2c8,#e6c6b2 60%,#c7b4a4)"></div>
  <div class="media-body">
    <h3>Sed ut perspiciatis under a<br>omnis iste natus error to</h3>
    <p>Lorem ipsum dolor sit ameti top<br>sed consectetur adipisicing elit</p>
    <div class="btn-outline-red">View more
      <svg class="arrow" viewBox="0 0 16 12" fill="none" stroke="#c4161c" stroke-width="2"><path d="M0 6h14M9 1l5 5-5 5"/></svg></div>
  </div>
</article>
<article class="abs media-card" style="top:2918px;left:92px">
  <div class="media-photo" role="img" aria-label="Photo of two hands holding each other" style="background:linear-gradient(160deg,#8fa2b4,#d2a58c 55%,#7a8a9c)"></div>
  <div class="media-body">
    <h3>Sed ut perspiciatis under a<br>omnis iste natus error to</h3>
    <p>Lorem ipsum dolor sit ameti top<br>sed consectetur adipisicing elit</p>
    <div class="btn-outline-red">View more
      <svg class="arrow" viewBox="0 0 16 12" fill="none" stroke="#c4161c" stroke-width="2"><path d="M0 6h14M9 1l5 5-5 5"/></svg></div>
  </div>
</article>
<article class="abs media-card" style="top:2918px;left:608px">
  <div class="media-photo" role="img" aria-label="Photo of an older woman with glasses smiling" style="background:linear-gradient(160deg,#c9ccc9,#9aa3a8 55%,#4e5a66)"></div>
  <div class="media-body">
    <h3>Sed ut perspiciatis under a<br>omnis iste natus error to</h3>
    <p>Lorem ipsum dolor sit ameti top<br>sed consectetur adipisicing elit</p>
    <div class="btn-outline-red">View more
      <svg class="arrow" viewBox="0 0 16 12" fill="none" stroke="#c4161c" stroke-width="2"><path d="M0 6h14M9 1l5 5-5 5"/></svg></div>
  </div>
</article>

<!-- events -->
<svg class="abs events-shape" width="1200" height="1120" viewBox="0 0 1200 1120">
  <polygon points="0,318 850,132 1200,470 1200,1120 0,1120" fill="var(--dark)"/>
  <polygon points="873,130 1200,4 1200,436" fill="var(--red)"/>
</svg>
<div class="abs footer-bg"></div>
<div class="abs mark-square" style="top:3530px;left:585px"></div>
<h2 class="abs center-title head" style="top:3572px;left:0">Latest Events</h2>
<p class="abs center-sub" style="top:3638px;left:0">Lorem ipsum dolor sit ameti consectetur adipisicing elit<br>sed do eiusmod tempor incididunt ut labore et</p>
<svg class="abs side-arrow" style="top:3849px;left:18px" viewBox="0 0 50 20" fill="none" stroke="#fff" stroke-width="2"><path d="M48 10H2M10 2 2 10l8 8"/></svg>
<svg class="abs side-arrow" style="top:3849px;left:1132px" viewBox="0 0 50 20" fill="none" stroke="#fff" stroke-width="2"><path d="M2 10h46M40 2l8 8-8 8"/></svg>

<article class="abs event-card" style="left:92px">
  <div class="event-photo" role="img" aria-label="Photo of a woman using a wheelchair in the street" style="background:linear-gradient(180deg,#2f3a4a,#9aaabb 55%,#c7c9cc)"></div>
  <div class="event-date"><span class="day">24</span><span class="mon">Mar</span></div>
  <div class="event-body">
    <div class="event-by">Event By Mara Lindqvist</div>
    <h3>Sed ut perspiciatis under a<br>omnis iste natus error to</h3>
    <p>Lorem ipsum dolor sit ameti top<br>sed consectetur adipisicing elit</p>
    <div class="event-more">View more <svg class="arrow" viewBox="0 0 16 12" fill="none" stroke="#c4161c" stroke-width="2"><path d="M0 6h14M9 1l5 5-5 5"/></svg></div>
  </div>
</article>
<article class="abs event-card" style="left:439px">
  <div class="event-photo" role="img" aria-label="Photo of a man with a white cane walking in a park" style="background:linear-gradient(180deg,#8aa06a,#5d7a44 55%,#3e4e34)"></div>
  <div class="event-date"><span class="day">03</span><span class="mon">May</span></div>
  <div class="event-body">
    <div class="event-by">Event By Mara Lindqvist</div>
    <h3>Sed ut perspiciatis under a<br>omnis iste natus error to</h3>
    <p>Lorem ipsum dolor sit ameti top<br>sed consectetur adipisicing elit</p>
    <div class="event-more">View more <svg class="arrow" viewBox="0 0 16 12" fill="none" stroke="#c4161c" stroke-width="2"><path d="M0 6h14M9 1l5 5-5 5"/></svg></div>
  </div>
</article>
<article class="abs event-card" style="left:785px">
  <div class="event-photo" role="img" aria-label="Photo of a smiling boy sitting by a window" style="background:linear-gradient(160deg,#6a6e70,#8a6a4a 55%,#3a3430)"></div>
  <div class="event-date"><span class="day">12</span><span class="mon">Jun</span></div>
  <div class="event-body">
    <div class="event-by">Event By Mara Lindqvist</div>
    <h3>Sed ut perspiciatis under a<br>omnis iste natus error to</h3>
    <p>Lorem ipsum dolor sit ameti top<br>sed consectetur adipisicing elit</p>
    <div class="event-more">View more <svg class="arrow" viewBox="0 0 16 12" fill="none" stroke="#c4161c" stroke-width="2"><path d="M0 6h14M9 1l5 5-5 5"/></svg></div>
  </div>
</article>

<!-- donate -->
<div class="abs donate-band"></div>
<div class="abs donate-line"></div>
<div class="abs donate-text head"><span class="s1">Need help to</span><span class="s2">Improve accessibility</span></div>
<div class="abs donate-divider"></div>
<div class="abs donate-btn">Donate us now
  <svg class="arrow" viewBox="0 0 16 12" fill="none" stroke="#fff" stroke-width="2"><path d="M0 6h14M9 1l5 5-5 5"/></svg>
</div>

<!-- footer -->
<div class="abs brand footer-brand">
  <span class="brand-square"></span>
  <span class="brand-name">OPENWAY ASSOCIATION</span>
</div>
<div class="abs footer-social"><span></span><span></span><span></span></div>

<div class="abs footer-col" style="top:4530px;left:443px">
  <h4>Quick Links</h4>
  <ul><li>Home</li><li>Our Achievements</li><li>Media</li><li>Events</li></ul>
</div>
<div class="abs footer-col" style="top:4530px;left:672px">
  <h4>Other Links</h4>
  <ul><li>Privacy Policy</li><li>Terms &amp; Condition</li><li>FAQ</li><li>Contact</li></ul>
</div>
<div class="abs footer-col" style="top:4530px;left:901px;width:240px">
  <h4>Contact Info</h4>
  <div class="contact-row">
    <span class="contact-ico"><svg width="18" height="18" viewBox="0 0 24 24" fill="none" stroke="#fff" stroke-width="2"><path d="M12 22s7-7 7-12a7 7 0 0 0-14 0c0 5 7 12 7 12z"/><circle cx="12" cy="10" r="2.5"/></svg></span>
    <span>Route des Mélèzes 12<br>1870 Montvert</span>
  </div>
  <div class="contact-row">
    <span class="contact-ico"><svg width="18" height="18" viewBox="0 0 24 24" fill="none" stroke="#fff" stroke-width="2"><path d="M22 16.9v3a2 2 0 0 1-2.2 2 19.8 19.8 0 0 1-8.6-3.1 19.5 19.5 0 0 1-6-6A19.8 19.8 0 0 1 2.1 4.2 2 2 0 0 1 4.1 2h3a2 2 0 0 1 2 1.7c.1.9.4 1.8.7 2.7a2 2 0 0 1-.5 2.1L8 9.8a16 16 0 0 0 6 6l1.3-1.3a2 2 0 0 1 2.1-.5c.9.3 1.8.6 2.7.7a2 2 0 0 1 1.7 2z"/></svg></span>
    <span>Phone:<br>024-718-3356</span>
  </div>
</div>
<div class="abs footer-rule"></div>
<div class="abs copyright">Copyright © 2022 OpenWay Association. All rights reserved.</div>

</body>
</html>
```